Template Flyer- Corewell Stretch & Flow

I am wanting a template 1 page flyer designed to use on the back ground of newsletter (faded background) and for our advertising posters in A4, A3, for Facebook and Instagram compatibility.

I have loaded an example from another Studio called Pinegrove (file 3)- each time they have a new workshop to advertise a picture is placed in the little circle (so this is something I would want to do too where I can load a new picture each time a new workshop is running)- They have used the flyer like a water mark...I like this.

Our colour palette is what is on our logos and you can also visit our website for a feel for what we like www.corewellstretch.com.au

I need some of the designs edited a bit more and because of the time difference, there seems to be a 24hour period where we communicate with each other. May I please request another 2 days extension

Requirements
Must have
• Id like to have a picture in the back ground. My favourite back ground that has been produced so far is a background of both picture file 9 and 10 in either.
Nice to have
• 3 picture circles options to advertise the events/workshops I have each year.
• Brush stroke style circles (see picture attached)rather then smooth circles for the picture area (in a grey tone)
Should not have
• No BLACK colour writing or black circles

```html
<!DOCTYPE html>
<html lang="en">
<head>
<meta charset="utf-8">
<title>Yoga Workout – Corewell Stretch &amp; Flow</title>
<link href="https://fonts.googleapis.com/css2?family=Raleway:wght@400;500;600;700&display=swap" rel="stylesheet">
<style>
  :root {
    --teal: #2ba3c2;
    --teal-deep: #1f8fad;
    --ink: #4d4f52;
    --ink-soft: #5f6164;
    --ring: #b9bcbf;
    --rule: #9ea2a6;
    --bg-light: #f3f4f3;
    --bg-mat: #c9cdcb;
    --bg-bolster: #c6d0c4;
    --bg-floor: #dfe1df;
    --photo-a: #d9dcdb;
    --photo-b: #a9b7ad;
    --photo-c: #7c8f86;
  }
  html, body {
    margin: 0;
    padding: 0;
    overflow: hidden;
    background: #ffffff;
  }
  .flyer {
    position: relative;
    width: 849px;
    height: 1200px;
    overflow: hidden;
    font-family: "Raleway", Arial, sans-serif;
    color: var(--ink);
  }
  .flyer__backdrop {
    position: absolute;
    inset: 0;
    background:
      radial-gradient(ellipse 260px 120px at 70px 930px, var(--bg-bolster), transparent 70%),
      radial-gradient(ellipse 240px 110px at 790px 760px, var(--bg-bolster), transparent 70%),
      radial-gradient(ellipse 300px 130px at 160px 1120px, var(--bg-mat), transparent 70%),
      radial-gradient(ellipse 320px 140px at 760px 1080px, var(--bg-mat), transparent 70%),
      radial-gradient(ellipse 280px 160px at 90px 230px, var(--bg-mat), transparent 70%),
      radial-gradient(ellipse 260px 160px at 800px 300px, var(--bg-floor), transparent 70%),
      linear-gradient(180deg, var(--bg-light) 0%, var(--bg-floor) 60%, #e6e8e6 100%);
  }
  .feature-photo {
    position: absolute;
    left: 182px;
    top: 18px;
    width: 484px;
    height: 484px;
    border-radius: 50%;
    background:
      radial-gradient(circle at 65% 40%, var(--photo-b) 0%, transparent 45%),
      linear-gradient(160deg, var(--photo-a) 0%, var(--photo-b) 55%, var(--photo-c) 100%);
    box-shadow: 0 0 0 10px var(--ring), 0 4px 14px rgba(80,80,80,0.25);
  }
  .tagline {
    position: absolute;
    left: 0;
    right: 0;
    top: 578px;
    margin: 0;
    text-align: center;
    font-size: 36px;
    font-weight: 500;
    line-height: 45px;
    color: var(--ink);
  }
  .divider {
    position: absolute;
    left: 130px;
    width: 590px;
    height: 2px;
    background: var(--rule);
  }
  .divider--top { top: 684px; }
  .divider--bottom { top: 950px; }
  .event {
    position: absolute;
    left: 0;
    right: 0;
    top: 716px;
    text-align: center;
    color: var(--teal);
  }
  .event p, .event h1 { margin: 0; }
  .event__title {
    font-size: 48px;
    font-weight: 500;
    line-height: 56px;
  }
  .event__date {
    font-size: 44px;
    font-weight: 500;
    line-height: 56px;
  }
  .event__time {
    font-size: 38px;
    font-weight: 700;
    line-height: 54px;
    color: var(--teal-deep);
  }
  .event__price {
    font-size: 26px;
    font-weight: 500;
    line-height: 48px;
  }
  .contact {
    position: absolute;
    left: 0;
    right: 0;
    top: 979px;
    text-align: center;
    font-style: normal;
    font-size: 20px;
    line-height: 33px;
    color: var(--ink-soft);
  }
  .contact p { margin: 0; }
  .brand {
    position: absolute;
    left: 218px;
    top: 1116px;
    display: flex;
    align-items: center;
    gap: 14px;
  }
  .brand__dot {
    width: 56px;
    height: 56px;
    border-radius: 50%;
    background: var(--teal);
  }
  .brand__name {
    font-size: 38px;
    font-weight: 500;
    color: var(--teal);
  }
</style>
</head>
<body>
  <main class="flyer">
    <div class="flyer__backdrop" role="img" aria-label="Faded photo of a yoga studio floor with rolled mats, patterned bolsters and cork blocks"></div>

    <div class="feature-photo" role="img" aria-label="Circular photo of yoga mats with patterned bolsters and cork blocks for the featured workshop"></div>

    <p class="tagline">Pilates and yoga<br>for your mind, body &amp; soul.</p>

    <div class="divider divider--top"></div>

    <section class="event">
      <h1 class="event__title">Yoga WORKOUT</h1>
      <p class="event__date">SUNDAY 24th MARCH</p>
      <p class="event__time">6:30 PM- 8:30PM</p>
      <p class="event__price">40$ Regular Price</p>
    </section>

    <div class="divider divider--bottom"></div>

    <address class="contact">
      <p>18 Larchmont Road, Ashvale, VIC 3491</p>
      <p>T: (03) 5555 0148</p>
      <p>E: info at corewellstretch.com.au</p>
    </address>

    <div class="brand">
      <span class="brand__dot"></span>
      <span class="brand__name">Corewell Stretch &amp; Flow</span>
    </div>
  </main>
</body>
</html>
```